Redesign of business card for Cedar Ridge Mechanical

We are looking for a new design for our business cards for Cedar Ridge Mechanical. We are a plumbing & HVAC construction company, operating on the West Coast of Canada and USA. Logo attached.
Industry/Entity Type
Construction - Plumbing & HVAC
Contact Information for Business Card
Name, address, phone numbers, email, website address
Look and feel
Each slider illustrates characteristics of the customer's brand and the style your logo design should communicate.

```html
<!DOCTYPE html>
<html lang="en">
<head>
<meta charset="utf-8">
<title>Cedar Ridge Mechanical – Business Cards</title>
<link href="https://fonts.googleapis.com/css2?family=Mulish:wght@400;800&display=swap" rel="stylesheet">
<style>
  :root {
    --backdrop: #222222;
    --ink: #000000;
    --paper: #ffffff;
    --steel: #8a8a8a;
    --soft-text: #e6e6e6;
  }
  * { margin: 0; padding: 0; box-sizing: border-box; }
  html, body {
    width: 1200px; height: 780px; overflow: hidden;
    background: var(--backdrop);
    font-family: "Mulish", sans-serif;
  }
  .canvas { position: relative; width: 1200px; height: 780px; }

  .card { position: absolute; overflow: hidden; background: var(--paper); }

  /* Back: portrait card with wave and contact details */
  .card--back { left: 170px; top: 100px; width: 340px; height: 580px; }
  .card--back .waves { position: absolute; inset: 0; }
  .brand-mark {
    position: absolute; display: flex; align-items: center; gap: 12px;
  }
  .brand-mark__square { background: var(--ink); flex: none; }
  .brand-mark__name {
    color: var(--ink); font-weight: 800; text-transform: uppercase;
    line-height: 1.1; letter-spacing: 0.04em;
  }
  .card--back .brand-mark { left: 30px; top: 50px; }
  .card--back .brand-mark__square { width: 22px; height: 22px; }
  .card--back .brand-mark__name { font-size: 20px; }

  .contact {
    position: absolute; right: 26px; bottom: 32px; width: 280px;
    text-align: right; color: var(--soft-text);
  }
  .contact__name {
    color: var(--paper); font-weight: 800; font-size: 22px;
    letter-spacing: 0.05em; text-transform: uppercase;
  }
  .contact__role { font-size: 15px; margin-top: 4px; }
  .contact__address { font-size: 15px; margin-top: 14px; line-height: 1.35; }
  .contact__lines { list-style: none; margin-top: 18px; font-size: 15px; }
  .contact__lines li {
    display: flex; justify-content: flex-end; align-items: center;
    gap: 8px; margin-top: 6px;
  }
  .contact__icon { width: 16px; height: 16px; flex: none; }

  /* Front: landscape card with the company name */
  .card--front {
    left: 560px; top: 230px; width: 560px; height: 320px;
    display: flex; align-items: center; justify-content: center;
  }
  .card--front .brand-mark { position: static; gap: 20px; }
  .card--front .brand-mark__square { width: 44px; height: 44px; }
  .card--front .brand-mark__name { font-size: 34px; }
</style>
</head>
<body>
<main class="canvas">

  <section class="card card--back" aria-label="Card back with contact details">
    <svg class="waves" viewBox="0 0 340 580" preserveAspectRatio="none" aria-hidden="true">
      <path d="M0,190 C110,198 210,250 340,300 L340,310 C210,262 110,212 0,207 Z" fill="var(--ink)"/>
      <path d="M0,207 C110,217 210,268 340,316 L340,326 C210,280 110,234 0,230 Z" fill="var(--steel)"/>
      <path d="M0,230 C120,246 215,288 340,330 L340,580 L0,580 Z" fill="var(--ink)"/>
      <path d="M0,252 C130,272 220,302 340,338" fill="none" stroke="var(--paper)" stroke-width="2.5"/>
    </svg>

    <div class="brand-mark">
      <span class="brand-mark__square"></span>
      <span class="brand-mark__name">Cedar Ridge<br>Mechanical</span>
    </div>

    <div class="contact">
      <p class="contact__name">Daniel Hayes</p>
      <p class="contact__role">Managing Director</p>
      <p class="contact__address">Your address, City<br>State, Zip 1234</p>
      <ul class="contact__lines">
        <li>123 456 789
          <svg class="contact__icon" viewBox="0 0 16 16" aria-label="Phone">
            <circle cx="8" cy="8" r="8" fill="var(--paper)"/>
            <path d="M5,4 L7,4 L7.5,6.5 L6.5,7.3 C7,8.5 7.5,9 8.7,9.5 L9.5,8.5 L12,9 L12,11 C8,11.5 4.5,8 5,4 Z" fill="var(--ink)"/>
          </svg>
        </li>
        <li>info@cedarridgemech.com
          <svg class="contact__icon" viewBox="0 0 16 16" aria-label="Email">
            <circle cx="8" cy="8" r="8" fill="var(--paper)"/>
            <rect x="4" y="5" width="8" height="6" fill="none" stroke="var(--ink)" stroke-width="1.2"/>
            <path d="M4,5 L8,8.5 L12,5" fill="none" stroke="var(--ink)" stroke-width="1.2"/>
          </svg>
        </li>
        <li>www.cedarridgemech.com
          <svg class="contact__icon" viewBox="0 0 16 16" aria-label="Website">
            <circle cx="8" cy="8" r="8" fill="var(--paper)"/>
            <circle cx="8" cy="8" r="4.5" fill="none" stroke="var(--ink)" stroke-width="1.1"/>
            <ellipse cx="8" cy="8" rx="2" ry="4.5" fill="none" stroke="var(--ink)" stroke-width="1.1"/>
            <path d="M3.5,8 H12.5" stroke="var(--ink)" stroke-width="1.1"/>
          </svg>
        </li>
      </ul>
    </div>
  </section>

  <section class="card card--front" aria-label="Card front with company name">
    <div class="brand-mark">
      <span class="brand-mark__square"></span>
      <span class="brand-mark__name">Cedar Ridge<br>Mechanical</span>
    </div>
  </section>

</main>
</body>
</html>
```